Las Vegas transportation company needs a dynamic design for business cards

We are a transportation management company based in Las Vegas specializing in operating and maintaining public transit systems. We want to keep our existing logo but would like to design business cards that feature one or more transit systems (e.g. monorail, train, bus) and maybe also the Las Vegas landscape.

```html
<!DOCTYPE html>
<html lang="en">
<head>
<meta charset="utf-8">
<title>Northgate Transit Group – Business Card</title>
<link href="https://fonts.googleapis.com/css2?family=Cinzel:wght@400&family=Libre+Caslon+Text&family=Jost:wght@400&display=swap" rel="stylesheet">
<style>
  :root{
    --page:#e7e5e2;
    --frost:#d7dbe0;
    --frost-light:#eef0f3;
    --ink:#171c3d;
    --name:#e4ded3;
    --accent:#7f9fd0;
    --body:#d9dbe4;
    --icon:#8aa6d6;
    --scene-sky:#c9d3e2;
    --scene-glow:#e8d9c4;
    --scene-ground:#9aa6bd;
  }
  *{margin:0;padding:0;box-sizing:border-box}
  html,body{width:1200px;height:969px;overflow:hidden;background:var(--page)}
  .canvas{position:relative;width:1200px;height:969px}
  .card{
    position:absolute;left:160px;top:234px;width:880px;height:500px;
    border-radius:22px;overflow:hidden;
    background:linear-gradient(135deg,var(--frost-light),var(--frost));
    box-shadow:0 10px 30px rgba(0,0,0,.12);
  }
  .card-shapes{position:absolute;inset:0}
  .transit-scene{
    position:absolute;left:600px;top:372px;width:280px;height:128px;
    background:linear-gradient(180deg,rgba(201,211,226,0) 0%,var(--scene-sky) 35%,var(--scene-glow) 70%,var(--scene-ground) 100%);
    opacity:.55;
  }
  .contact{position:absolute;left:50px;top:140px;color:var(--body);font-family:"Jost",sans-serif}
  .contact__name{font-family:"Libre Caslon Text",serif;font-weight:400;font-size:29px;letter-spacing:.5px;color:var(--name);line-height:1}
  .contact__role{font-size:19px;color:var(--accent);margin-top:6px;line-height:1.1}
  .contact__rule{width:65px;height:2px;background:var(--name);margin:12px 0 14px}
  .contact__list{list-style:none}
  .contact__item{display:flex;align-items:flex-start;font-size:19px;line-height:24.5px}
  .contact__item svg{flex:0 0 14px;width:14px;height:16px;margin:4px 14px 0 4px;fill:var(--icon)}
  .brand{
    position:absolute;left:470px;top:232px;width:350px;text-align:center;
    font-family:"Cinzel",serif;font-weight:400;color:var(--ink);
  }
  .brand__main{font-size:46px;line-height:1;letter-spacing:0}
  .brand__sub{font-size:17px;letter-spacing:5px;margin-top:14px;line-height:1}
</style>
</head>
<body>
<div class="canvas">
  <div class="card">
    <div class="transit-scene" role="img" aria-label="Las Vegas skyline at dusk with a monorail, train and city bus"></div>
    <svg class="card-shapes" width="880" height="500" viewBox="0 0 880 500" aria-hidden="true">
      <defs>
        <linearGradient id="navyFill" x1="0" y1="0" x2="1" y2="1">
          <stop offset="0" stop-color="#1e2450"/>
          <stop offset=".6" stop-color="#2a3163"/>
          <stop offset="1" stop-color="#10142f"/>
        </linearGradient>
      </defs>
      <path d="M560 0 H880 V500 H760 C730 500 712 480 700 450 L600 120 C585 70 575 20 560 0 Z" fill="#ffffff" opacity=".28"/>
      <path d="M390 0 H560 C590 0 605 20 615 50 L740 440 C752 480 770 500 800 500 H640 C610 500 590 480 578 450 L455 60 C445 25 425 0 390 0 Z" fill="#ffffff" opacity=".22"/>
      <path d="M0 0 H310 C340 0 355 20 365 50 L500 440 C512 480 535 500 575 500 H0 Z" fill="url(#navyFill)"/>
    </svg>

    <div class="contact">
      <h1 class="contact__name">DANIEL BROOKS</h1>
      <p class="contact__role">President</p>
      <div class="contact__rule"></div>
      <ul class="contact__list">
        <li class="contact__item"><svg viewBox="0 0 14 16"><path d="M7 0a5.5 5.5 0 0 0-5.5 5.5C1.5 9.5 7 16 7 16s5.5-6.5 5.5-10.5A5.5 5.5 0 0 0 7 0zm0 7.8a2.3 2.3 0 1 1 0-4.6 2.3 2.3 0 0 1 0 4.6z"/></svg><span>1420 Alder Street<br>Las Vegas, Nevada 89101</span></li>
        <li class="contact__item"><svg viewBox="0 0 14 16"><path d="M3 1l2.5 3-1.5 1.5c.8 2 2.5 3.7 4.5 4.5L10 8.5l3 2.5-1.5 2.5C7 13.5 1.5 8 1 3.5z"/></svg><span>555-214-7720</span></li>
        <li class="contact__item"><svg viewBox="0 0 14 16"><path d="M3 0h8a1 1 0 0 1 1 1v14a1 1 0 0 1-1 1H3a1 1 0 0 1-1-1V1a1 1 0 0 1 1-1zm1 2v10h6V2zm3 11a1 1 0 1 0 0 2 1 1 0 0 0 0-2z"/></svg><span>555-618-3094</span></li>
        <li class="contact__item"><svg viewBox="0 0 14 16"><path d="M3 2h8v4H3zM1 7h12v6h-2v-2H3v2H1zm3 5h6v3H4z"/></svg><span>555-402-1186</span></li>
        <li class="contact__item"><svg viewBox="0 0 14 16"><path d="M0 4h14v9H0zm1 1l6 4 6-4v-.2H1z"/></svg><span>hello@northgatetransit.com</span></li>
        <li class="contact__item"><svg viewBox="0 0 14 16"><path d="M7 2a6 6 0 1 0 0 12A6 6 0 0 0 7 2zm-1 2c1 1 1 2 0 3s-3 0-3 2 2 2 2 3c-2-.5-3.5-2.5-3.5-4.5S3.5 4 6 4zm3 0c1.5.8 2.5 2.2 2.5 4 0 1-.5 2-1.2 2.8C9.5 10 9 9 8 9s-1-2 0-2.5S9 5 9 4z"/></svg><span>northgatetransit.com</span></li>
      </ul>
    </div>

    <div class="brand">
      <div class="brand__main">NORTHGATE</div>
      <div class="brand__sub">TRANSIT GROUP</div>
    </div>
  </div>
</div>
</body>
</html>
```